Bed Company needs business card

Hello, we are a bed company that makes specialized magnets for beds. We are an alternative healing company. I need a modern and upscale business card. Please incorporate my logo for the card.

Accepted file formats are AI, EPS, and Press-Ready PDFS.

Please include all fonts or convert them to outlines regardless of file type.

If you are designing the card in Photoshop the file Must be 1200dpi.

I am open to anything for the business card.  I really like all of your designs and if you want to change the color of the logo, you can.  I will be making the final selection by Friday.  Thank You for all of your designs.  Feel Free to submit different color logos if you want.  

Reason: I will make a decision Final on Friday April 20th. 2012. Good Luck and Thank you all for the designs.

Target Market(s)

My target Market is people, who are looking for alternative healing.

Industry/Entity Type

Business

Requirements
Must have
• My logo must be incorporated. The front card must have

Name
Job Title

Address
Work
Cell
Fax
email
web

Just put in fake info for the card.

The back of the card. I want the logo on the back with color. I just want it to look modern and cool.

```html
<!DOCTYPE html>
<html lang="en">
<head>
<meta charset="utf-8">
<title>Restful Field – Business Card</title>
<link rel="stylesheet" href="https://fonts.googleapis.com/css2?family=Open+Sans:wght@400;600;700&display=swap">
<style>
  :root {
    --bg: #d4d4d4;
    --card: #ffffff;
    --green-dark: #0b6333;
    --green-light: #51b848;
    --text: #3a3a3a;
    --title: #1f7a35;
  }
  * { margin: 0; padding: 0; box-sizing: border-box; }
  html, body { width: 1200px; height: 900px; overflow: hidden; }
  body {
    background: var(--bg);
    font-family: "Open Sans", Arial, sans-serif;
    position: relative;
  }
  .card {
    position: absolute;
    top: 291px;
    width: 509px;
    height: 318px;
    background: var(--card);
    box-shadow: 2px 3px 4px rgba(0,0,0,0.3);
    overflow: hidden;
  }
  .card--front { left: 74px; }
  .card--back { left: 617px; }
  .color-panel {
    position: absolute;
    left: 286px;
    top: 0;
    width: 223px;
    height: 318px;
    background: linear-gradient(160deg, var(--green-dark) 0%, var(--green-light) 70%);
  }
  .holder-name {
    position: absolute;
    left: 48px;
    top: 50px;
    font-size: 26px;
    font-weight: 400;
    color: var(--text);
  }
  .holder-title {
    position: absolute;
    left: 102px;
    top: 84px;
    font-size: 16px;
    color: var(--title);
  }
  .accent-bar {
    position: absolute;
    left: 24px;
    top: 133px;
    width: 5px;
    height: 143px;
    background: var(--green-light);
  }
  .contact {
    position: absolute;
    left: 55px;
    top: 138px;
    font-size: 13px;
    line-height: 17.5px;
    color: var(--text);
  }
  .contact-row { display: flex; }
  .contact-label { width: 32px; }
  .contact-sep { width: 19px; }
  .contact-email { margin-top: 3px; }
  .address {
    position: absolute;
    left: 55px;
    top: 239px;
    font-size: 9.5px;
    line-height: 13px;
    color: var(--text);
  }
  .website {
    position: absolute;
    right: 8px;
    bottom: 8px;
    font-size: 12.5px;
    color: #ffffff;
    letter-spacing: 0.3px;
  }
  .brand {
    position: absolute;
    left: 36px;
    top: 124px;
    display: flex;
    align-items: center;
    gap: 10px;
  }
  .brand-square {
    width: 30px;
    height: 30px;
    background: var(--green-dark);
  }
  .brand-text { display: flex; flex-direction: column; }
  .brand-name {
    font-size: 25px;
    font-weight: 700;
    color: var(--green-light);
    line-height: 28px;
  }
  .brand-tagline {
    font-size: 10px;
    color: var(--green-light);
    letter-spacing: 0.6px;
    align-self: flex-end;
  }
</style>
</head>
<body>
  <section class="card card--front">
    <h1 class="holder-name">Daniel Hayes</h1>
    <p class="holder-title">director</p>
    <div class="accent-bar"></div>
    <div class="contact">
      <div class="contact-row"><span class="contact-label">tel</span><span class="contact-sep">:</span><span>(999) 999 999</span></div>
      <div class="contact-row"><span class="contact-label">cell</span><span class="contact-sep">:</span><span>(999) 999 000</span></div>
      <div class="contact-row"><span class="contact-label">fax</span><span class="contact-sep">:</span><span>(999) 000 000</span></div>
      <div class="contact-email">hello@restfulfield.com</div>
    </div>
    <p class="address">May 14-16, 2013, Lakeside Hall East,<br>Denver CO, Booth 208</p>
    <div class="color-panel" role="img" aria-label="Brand colour panel"></div>
    <p class="website">www.restful-field.com</p>
  </section>

  <section class="card card--back">
    <div class="brand">
      <div class="brand-square"></div>
      <div class="brand-text">
        <span class="brand-name">Restful Field</span>
        <span class="brand-tagline">Alternative Healing</span>
      </div>
    </div>
    <div class="color-panel" role="img" aria-label="Brand colour panel"></div>
  </section>
</body>
</html>
```